design a construction company business card

Design business card around our logo. Card must have all the typical info: name, title, address, phone, email, business name, etc. Somewhere on the card I would like to see our motto "Grounded in trust... Driven by craftsmanship." Consider adding a splash of bright orange to the card to complement the blues and silvers/grays in the logo. We are open to metallic inks, textures, etc. We would like to see options on both light and dark backgrounds. The font in the logo is Euro Technic Extended Regular.

```html
<!DOCTYPE html>
<html lang="en">
<head>
<meta charset="utf-8">
<title>Kestrel Contracting – Business Card</title>
<link rel="stylesheet" href="https://fonts.googleapis.com/css2?family=Krona+One&family=Michroma&display=swap">
<style>
  :root {
    --stage: #2b2b2c;
    --card: #232324;
    --card-edge: #1a1a1b;
    --ink-white: #f2f2f2;
    --ink-grey: #9a9ca0;
    --brand-blue: #2f74d0;
    --band-blue: #2a6cd6;
    --divider: #d8d8d8;
  }
  * { margin: 0; padding: 0; box-sizing: border-box; }
  html, body { width: 1200px; height: 901px; overflow: hidden; background: var(--stage); }
  .canvas {
    position: relative; width: 1200px; height: 901px;
    background: var(--stage);
    font-family: "Michroma", sans-serif;
  }
  .card {
    position: absolute; background: var(--card);
    box-shadow: 0 14px 30px rgba(0,0,0,.45);
    border-bottom: 6px solid var(--card-edge);
    overflow: hidden;
  }
  /* front */
  .card--front { left: 290px; top: 40px; width: 620px; height: 354px; }
  .wordmark { position: absolute; left: 0; right: 0; top: 118px; text-align: center; }
  .wordmark__name {
    font-family: "Michroma", sans-serif; font-size: 46px; letter-spacing: 6px;
    color: var(--brand-blue); line-height: 1;
  }
  .wordmark__sub {
    display: flex; align-items: center; justify-content: center; gap: 8px;
    margin-top: 10px; font-size: 14px; letter-spacing: 1px; color: var(--ink-grey);
  }
  .wordmark__sub::before, .wordmark__sub::after {
    content: ""; width: 18px; height: 1px; background: var(--ink-grey);
  }
  .motto-band {
    position: absolute; left: 150px; top: 300px; width: 410px; height: 20px;
    background: var(--band-blue); transform: skewX(-20deg);
    display: flex; align-items: center; justify-content: center;
  }
  .motto-band span {
    transform: skewX(20deg); font-size: 10.5px; letter-spacing: 1px; color: var(--ink-white);
    white-space: nowrap;
  }
  /* back */
  .card--back { left: 240px; top: 444px; width: 720px; height: 411px; }
  .identity { position: absolute; right: 400px; top: 148px; text-align: right; }
  .identity__name {
    font-family: "Krona One", sans-serif; font-size: 27px; color: var(--ink-white); letter-spacing: 1px;
    white-space: nowrap;
  }
  .identity__title { margin-top: 10px; font-size: 17px; color: var(--brand-blue); }
  .divider { position: absolute; left: 338px; top: 180px; width: 2px; height: 56px; background: var(--divider); }
  .contacts { position: absolute; left: 356px; top: 176px; list-style: none; }
  .contacts li {
    display: flex; align-items: center; gap: 12px;
    font-size: 15px; color: var(--ink-white); height: 22px; white-space: nowrap;
  }
  .contacts svg { width: 12px; height: 12px; fill: var(--brand-blue); flex: none; }
  .contacts .accent { color: var(--brand-blue); }
  .footer {
    position: absolute; left: 30px; bottom: 42px;
    display: flex; align-items: center; gap: 10px; font-size: 15px; color: var(--ink-white);
    white-space: nowrap;
  }
  .footer__brand { font-size: 12px; letter-spacing: 1px; color: var(--ink-white); }
  .footer__sep { color: var(--brand-blue); }
</style>
</head>
<body>
<div class="canvas">

  <section class="card card--front" aria-label="Card front">
    <div class="wordmark">
      <div class="wordmark__name">KESTREL</div>
      <div class="wordmark__sub">CONTRACTING, INC.</div>
    </div>
    <div class="motto-band"><span>“Grounded in trust... Driven by craftsmanship.”</span></div>
  </section>

  <section class="card card--back" aria-label="Card back">
    <div class="identity">
      <div class="identity__name">MARCUS HALE</div>
      <div class="identity__title">Ceo &amp; Founder</div>
    </div>
    <div class="divider"></div>
    <ul class="contacts">
      <li>
        <svg viewBox="0 0 12 12" aria-hidden="true"><path d="M2.5 0.8 4.4 3 3.5 4.4c.7 1.6 2 2.9 3.6 3.6L8.5 7.1l2.2 1.9-1 2C5.2 11 1 6.8.8 2.1z"/></svg>
        000 111 2223
      </li>
      <li>
        <svg viewBox="0 0 12 12" aria-hidden="true"><path d="M0 2h12v8H0zM1 3v.3l5 3.3 5-3.3V3zM1 4.5V9h10V4.5L6 7.8z"/></svg>
        urname@email.com
      </li>
      <li>
        <svg viewBox="0 0 12 12" aria-hidden="true"><circle cx="6" cy="6" r="5.5"/></svg>
        <span>www.<span class="accent">ursitename</span>.com</span>
      </li>
    </ul>
    <div class="footer">
      <span class="footer__brand">KESTREL</span>
      <span class="footer__sep">-</span>
      <span>Your Street Address, UnitedStates, 1234</span>
    </div>
  </section>

</div>
</body>
</html>
```